Modern card design needed for building development company

We are looking for a sharp modern new look for our business cards.
We are a New Zealand based company called TKR Ventures NZ LTD that specialises in subdividing large sections, housing and commercial buildings.
We have attached a photo of the current logo and would like to see it improved somehow as it looks a bit dated.
We are open to any colours.

Target Market(s)

Investors, Property buyers

Industry/Entity Type

Investment

Contact Information for Business Card

TKR VENTURES NZ LTD
www.tkrventuresnz.co.nz

Damon Whitcombe
Phone +64 21 938 104
Email dpwhitcombe@korumail.co.nz

Font styles to use
Serif
Sans Serif

Colors
0792cd
33a6d7
85cae6
6b449b
886aae
f04a50
ec1f27
f37122
f68d4d

Requirements
Must have
• Please try and make the logo more modern or if you have a similar one we would like to see it.

```html
<!DOCTYPE html>
<html lang="en">
<head>
<meta charset="utf-8">
<title>TKR Ventures NZ LTD – Business Card</title>
<link rel="stylesheet" href="https://fonts.googleapis.com/css2?family=Montserrat:wght@600;700&family=Work+Sans:wght@400&display=swap">
<style>
  :root {
    --page-bg: #d8cec3;
    --card-bg: #eee8e1;
    --card-edge: #f8f4ef;
    --band: #3b3836;
    --accent: #9b2733;
    --accent-dark: #6e1a24;
    --ink: #3a3633;
    --muted: #6d6660;
    --band-text: #d2bd9f;
    --band-text-light: #e2d5c3;
  }
  * { box-sizing: border-box; margin: 0; padding: 0; }
  html, body { width: 1200px; height: 1047px; overflow: hidden; }
  body { background: var(--page-bg); position: relative; font-family: "Work Sans", sans-serif; }

  .card {
    position: absolute; left: 80px; top: 241px;
    width: 1040px; height: 565px;
    background: var(--card-bg);
    border: 2px solid var(--card-edge);
    border-radius: 18px;
    overflow: hidden;
    box-shadow: 0 10px 30px rgba(60, 45, 30, 0.18);
  }

  .brand {
    position: absolute; right: 46px; top: 150px;
    display: flex; flex-direction: column; align-items: center; gap: 22px;
  }
  .brand-mark {
    width: 74px; height: 74px; background: var(--accent);
  }
  .brand-name {
    font-family: "Montserrat", sans-serif; font-weight: 600;
    font-size: 19px; letter-spacing: 1.5px; color: var(--ink);
  }

  .holder { position: absolute; left: 50px; top: 290px; }
  .holder-name {
    font-family: "Montserrat", sans-serif; font-weight: 700;
    font-size: 33px; letter-spacing: 0.5px; color: var(--accent);
    text-transform: uppercase; line-height: 1.15;
  }
  .holder-role { font-size: 23px; color: var(--muted); margin-top: 2px; }

  .info-band {
    position: absolute; left: 0; right: 0; top: 381px; height: 154px;
    background: var(--band);
  }
  .info-tab { position: absolute; left: 0; top: 0; width: 42px; height: 154px; }

  .contact-list {
    position: absolute; left: 56px; top: 28px; list-style: none;
    display: flex; flex-direction: column; gap: 6px;
  }
  .contact-item {
    display: flex; align-items: center; gap: 14px;
    font-size: 24px; color: var(--band-text); line-height: 26px;
  }
  .contact-icon { width: 17px; height: 17px; flex: none; }

  .address {
    position: absolute; right: 46px; top: 28px; text-align: right;
    font-size: 24px; line-height: 32px; color: var(--band-text-light);
    font-style: normal;
  }
</style>
</head>
<body>
  <article class="card">
    <div class="brand">
      <div class="brand-mark"></div>
      <div class="brand-name">TKR VENTURES NZ LTD</div>
    </div>

    <div class="holder">
      <h1 class="holder-name">Damon Whitcombe</h1>
      <p class="holder-role">Director</p>
    </div>

    <section class="info-band">
      <svg class="info-tab" viewBox="0 0 42 154" aria-hidden="true">
        <polygon points="0,0 14,0 36,22 36,132 14,154 0,154" fill="var(--accent)"/>
        <polyline points="14,0 36,22 36,132 14,154" fill="none" stroke="var(--band-text)" stroke-width="2"/>
      </svg>

      <ul class="contact-list">
        <li class="contact-item">
          <svg class="contact-icon" viewBox="0 0 24 24" aria-hidden="true"><path d="M6.6 10.8a15.1 15.1 0 0 0 6.6 6.6l2.2-2.2a1 1 0 0 1 1-.25 11.4 11.4 0 0 0 3.6.57 1 1 0 0 1 1 1V20a1 1 0 0 1-1 1A17 17 0 0 1 3 4a1 1 0 0 1 1-1h3.5a1 1 0 0 1 1 1c0 1.25.2 2.45.57 3.57a1 1 0 0 1-.25 1z" fill="var(--band-text)"/></svg>
          <span>+64 21 938 104</span>
        </li>
        <li class="contact-item">
          <svg class="contact-icon" viewBox="0 0 24 24" aria-hidden="true"><rect x="2.5" y="5" width="19" height="14" rx="1.5" fill="none" stroke="var(--band-text)" stroke-width="2"/><polyline points="3,6 12,13 21,6" fill="none" stroke="var(--band-text)" stroke-width="2"/></svg>
          <span>dpwhitcombe@korumail.co.nz</span>
        </li>
        <li class="contact-item">
          <svg class="contact-icon" viewBox="0 0 24 24" aria-hidden="true"><g fill="none" stroke="var(--band-text)" stroke-width="1.8"><circle cx="12" cy="12" r="9.5"/><ellipse cx="12" cy="12" rx="4" ry="9.5"/><line x1="2.5" y1="12" x2="21.5" y2="12"/></g></svg>
          <span>www.tkrventuresnz.co.nz</span>
        </li>
      </ul>

      <address class="address">
        PO BOX 48215<br>
        Albany Auckland<br>
        New Zealand
      </address>
    </section>
  </article>
</body>
</html>
```